Bry7Legal Letterhead

Need a new letterhead for my law firm.
IDENTIFYING INFORMATION BELOW:
Anselmo R Quintara III
Attorney at Law
Address: 2847 Larkspur Blvd, Ste 300, Dallas, TX 75204
Phone: 877-482-6017
Fax: 469-738-1452
Email: bry@bry7legal.example
Website: www.bry7legal.example

Colors
0054AA
0677BA
7BADD7
CADEEF
E8F1F8

Requirements
Must have
• Logo needs to be on the letterhead, along with identifying information which is included in the project description.

```html
<!DOCTYPE html>
<html lang="en">
<head>
<meta charset="utf-8">
<title>Bry7Legal Letterhead</title>
<link href="https://fonts.googleapis.com/css2?family=Arimo:wght@400;700&family=Montserrat:wght@300;400;800&display=swap" rel="stylesheet">
<style>
  :root {
    --bg: #acabab;
    --paper: #ffffff;
    --ink: #111111;
    --band: #000000;
    --bright-blue: #1a8ee0;
    --body-grey: #8a8a8a;
    --label-grey: #555555;
    --sig-fill: #eef1f4;
  }
  * { box-sizing: border-box; margin: 0; padding: 0; }
  html, body { width: 1200px; height: 1200px; overflow: hidden; background: var(--bg); }
  .sheet {
    position: absolute; left: 230px; top: 75px;
    width: 739px; height: 1045px;
    background: var(--paper);
    font-family: "Montserrat", sans-serif;
  }
  .band { position: absolute; left: 0; top: 0; width: 739px; height: 160px; }
  .brand {
    position: absolute; left: 48px; top: 58px;
    font-family: "Montserrat", sans-serif; font-weight: 800;
    font-size: 32px; line-height: 1; color: var(--ink); letter-spacing: 0.5px;
  }
  .brand-mark {
    display: inline-block; width: 12px; height: 12px;
    background: var(--bright-blue); margin-left: 8px; vertical-align: 3px;
  }
  .attorney {
    position: absolute; left: 406px; top: 50px;
    font-family: "Arimo", sans-serif; color: #fff; font-size: 12px; line-height: 14.4px;
  }
  .attorney-name { color: var(--bright-blue); font-weight: 700; }
  .attorney-address { margin-top: 9px; line-height: 15.5px; }
  .divider { position: absolute; left: 563px; top: 49px; width: 1px; height: 65px; background: #fff; }
  .contacts {
    position: absolute; left: 576px; top: 49px; list-style: none;
    font-family: "Arimo", sans-serif; color: #fff; font-size: 12px; line-height: 17.6px;
  }
  .contacts li { display: flex; align-items: center; gap: 6px; }
  .contacts svg { width: 9px; height: 9px; fill: var(--bright-blue); flex: none; }
  .letter { position: absolute; left: 75px; top: 238px; width: 590px; height: 580px; }
  .date { position: absolute; right: 0; top: 0; font-size: 10.4px; color: var(--label-grey); }
  .to-label { position: absolute; left: 0; top: 0; font-size: 12.5px; letter-spacing: 2px; color: var(--label-grey); }
  .recipient-name { position: absolute; left: 0; top: 21px; font-size: 12.5px; color: var(--bright-blue); }
  .recipient-lines { position: absolute; left: 0; top: 42px; font-size: 9.6px; line-height: 16.3px; color: var(--body-grey); }
  .body-text { position: absolute; left: 0; top: 142px; width: 590px; }
  .body-text p {
    font-size: 10.6px; font-weight: 300; line-height: 13.1px;
    color: var(--body-grey); text-align: justify; margin-bottom: 13.1px;
  }
  .signature { position: absolute; left: -2px; top: 512px; width: 128px; height: 30px; background: var(--sig-fill); }
  .signer-name { position: absolute; left: -2px; top: 546px; font-size: 12px; color: #333; letter-spacing: 0.3px; }
  .signer-title { position: absolute; left: -2px; top: 563px; font-size: 9.6px; color: var(--body-grey); }
</style>
</head>
<body>
<main class="sheet">
  <svg class="band" viewBox="0 0 739 160" aria-hidden="true">
    <polygon points="250,24 739,24 739,137 250,137 305,80" fill="var(--band)"/>
  </svg>

  <div class="brand">Bry7Legal<span class="brand-mark"></span></div>

  <div class="attorney">
    <div class="attorney-name">Anselmo R Quintara III</div>
    <div>Attorney at Law</div>
    <div class="attorney-address">2847 Larkspur Blvd<br>Ste 300, Dallas, TX 75204</div>
  </div>
  <div class="divider"></div>
  <ul class="contacts">
    <li><svg viewBox="0 0 12 12"><path d="M2.5 0.5l2 2.5-1.2 1.3c.7 1.6 1.8 2.7 3.4 3.4L8 6.5l2.5 2-1 2.5C5 10.5 1.5 7 1 2.5z"/></svg>877-482-6017</li>
    <li><svg viewBox="0 0 12 12"><path d="M3 0h6v3H3zM1 4h10v5H9V7H3v2H1zM3.5 8h5v4h-5z"/></svg>469-738-1452</li>
    <li><svg viewBox="0 0 12 12"><path d="M0 2h12v8H0zM1 3l5 3.5L11 3v-.2L6 5.6 1 2.8z" fill-rule="evenodd"/></svg>bry@bry7legal.example</li>
    <li><svg viewBox="0 0 12 12"><circle cx="6" cy="6" r="5.5"/></svg>www.bry7legal.example</li>
  </ul>

  <section class="letter">
    <div class="date">Friday, 01/01/2018</div>
    <div class="to-label">TO</div>
    <div class="recipient-name">Delia Farnsworth</div>
    <div class="recipient-lines">Human Resources<br>Northvale Systems Inc.<br>412-B Orchard Lane, Hollins<br>E47 USA</div>

    <div class="body-text">
      <p>Lorem ipsum dolor sit amet, consectetuer adipiscing elit, sed diam nonmmy nibh euismod tincidunt ut laoreet dolore magna aliquam erat volutpat. Ut wisi enim ad minim veniam, quis nostrud exerci tationmcorper suscipit lobortis nisl ut aliquip ex ea commodo consequat. Duis autem vel eum iriure dolor in hendrerit in vulputate velit esse molestie consequat, vel illum dolore eu feugiat nulla facilisis at vero eros et accumsan et iusto odio dignissim qui blandit praesent luptatum zzril delenit augue duis dolore te feugait nulla facilisi.</p>
      <p>Nam liber tempor cum soluta nobis eleifend option congue nihil imprdiet doming id quod mazim placerat facer possim assum. Typi non habent claritatem insitam;</p>
      <p>Est usus legentis in iis qui facit eorum claritatem.</p>
      <p>Investigationes demonstraverunt lectores legere me lius quod ii legunt saepius. Claritas est etiam processus dynamicus, qui sequitur mutationem consuetudium lectorum. Mirum est notare quam littera gothica, quam nunc putamus parum claram, anteposuerit litterarum formas humanitatis per seacula quarta decima et quinta decima. Eodem modo typi, qui nunc nobis videntur parum clari, fiant sollemnes in futurum.</p>
      <p>consectetuer adipiscing elit, sed diam nonummy nibh euismod tincidunt ut laoreet dolore magna aliquam erat volutpat. Ut wisi enim ad minim veniam, quis nostrud exerci tation ullamcorper suscipit lobortis nisl ut aliquip ex ea commodo consequat. Duis autem vel eum iriure dolor in hendrerit in vulputate velit esse molestie consequat, vel illum dolore eu feugiat nulla facilisis at vero eros et accumsan et iusto odio dignissim qui blandit praesent luptatum zzril delenit augue duis dolore te feugait nulla facilisi.</p>
      <p>Nam liber tempor cum soluta nobis eleifend option congue nihil imperdiet .</p>
    </div>

    <div class="signature" role="img" aria-label="Handwritten signature of the sender"></div>
    <div class="signer-name">Peter Ashcombe</div>
    <div class="signer-title">Managing Director</div>
  </section>
</main>
</body>
</html>
```